Velmor Spire Nine Flash website

we need a website to cater to 2 aspect of the business. We have Velmor spire residence and velmor spire office. For the office, we will get their inquire and arrange a face to face meetup to show them the office area for rent. For the residence side, it will need to be like staylane or roomvio.com. we want to allow them to book online for the date they need. We have a total of 10 different room configurations starting at $70 per night and up depending on the size of the room. example of the design is https://brisquelodge.com/

Target Market(s)

the website should have detail information on the layout, designs, and luxury of the building.

Industry/Entity Type

office and service appartment rental/lease

Coding

Coded - Design and coding required

Number of Pages Required

5+ page

Requirements
Must have
• a luxury perspective
Nice to have
• example https://brisquelodge.com/

```html
<!DOCTYPE html>
<html lang="en">
<head>
<meta charset="utf-8">
<title>Velmor Spire Nine</title>
<link href="https://fonts.googleapis.com/css2?family=Cinzel:wght@400;600&family=Roboto:wght@400;500;700&display=swap" rel="stylesheet">
<style>
:root{
  --gold:#d19a26;
  --gold-dark:#b8841c;
  --ink:#1a1a1a;
  --text:#333;
  --muted:#666;
  --page:#ebebeb;
  --soft:#f4f4f4;
  --white:#fff;
}
*{box-sizing:border-box;margin:0;padding:0}
html,body{width:1200px;height:4264px;overflow:hidden;background:var(--page);font-family:"Roboto",Arial,sans-serif;color:var(--text)}
.panel{position:absolute;left:93px;width:1014px;background:var(--white);overflow:hidden;box-shadow:0 4px 18px rgba(0,0,0,.12)}
.abs{position:absolute}
.c{position:absolute;transform:translateX(-50%);text-align:center;white-space:nowrap}
.serif{font-family:"Cinzel",Georgia,serif}
.photo{position:absolute}
.logo-name{font-family:"Cinzel",Georgia,serif;color:var(--gold);font-size:22px;letter-spacing:.5px;white-space:nowrap}
.btn{position:absolute;display:flex;align-items:center;justify-content:center;font-size:11px;font-weight:700;letter-spacing:.3px;text-transform:uppercase}
.btn-outline-light{border:2px solid var(--white);color:var(--white)}
.btn-gold{background:var(--gold);color:var(--white)}
.btn-outline-gold{border:1.5px solid var(--gold);color:var(--ink);background:var(--white)}
.btn-dark{background:var(--ink);color:var(--white)}
.split-title{font-family:"Cinzel",Georgia,serif;font-size:30px;color:var(--white);text-shadow:0 1px 4px rgba(0,0,0,.3)}
.split-text{font-size:14.5px;line-height:24px;color:var(--white)}
.footer{position:absolute;left:0;width:1014px;height:371px;color:var(--white)}
.footer .nav a{position:absolute;top:64px;font-size:11.5px;font-weight:700;color:var(--white);text-decoration:none;white-space:nowrap}
.footer .rule{position:absolute;left:93px;width:828px;height:1px;background:#3a3a3a}
.footer .vdiv{position:absolute;top:128px;height:158px;width:1px;background:#3a3a3a}
.footer .label{font-size:13px;font-weight:700}
.footer .label::after{content:"";display:block;width:22px;height:2px;background:var(--gold);margin:5px auto 0}
.footer .info{font-size:12px;line-height:21px}
.footer .copy{font-size:11px;top:324px}
.social{position:absolute;width:28px;height:28px;border-radius:50%;border:1.5px solid #bbb}
.social.on{background:var(--gold);border-color:var(--gold)}
.topbar{position:absolute;left:0;top:0;width:1014px;height:40px;background:var(--ink);color:var(--white);font-size:11px}
.mainnav{position:absolute;left:0;top:40px;width:1014px;height:66px;background:var(--white);border-bottom:1px solid #eee}
.mainnav a{position:absolute;top:0;height:66px;display:flex;align-items:center;font-size:12px;font-weight:700;color:var(--ink);text-decoration:none}
.h-section{font-family:"Cinzel",Georgia,serif;color:var(--ink);font-size:36px;font-weight:400}
.underline{position:absolute;height:3px;background:var(--gold)}
.body-p{font-size:11.8px;line-height:22px;color:var(--muted);text-align:justify}
.card{position:absolute;width:258px;background:var(--white);box-shadow:0 2px 10px rgba(0,0,0,.1)}
.solution{top:1361px;height:295px;border:1.5px solid var(--gold)}
.solution .tag{position:absolute;left:42px;top:-14px;width:172px;height:34px;background:var(--gold);color:var(--white);font-size:11px;font-weight:700;display:flex;align-items:center;justify-content:center}
.solution p{position:absolute;left:14px;right:14px;top:44px;font-size:11.8px;line-height:21px;text-align:center;color:var(--text)}
.solution .photo{left:8px;right:8px;top:124px;height:163px}
.testi{top:1887px;height:219px;padding:0 20px}
.stars{position:absolute;left:20px;top:20px;color:var(--gold);font-size:11px;letter-spacing:1px}
.testi p{position:absolute;left:20px;right:20px;top:44px;font-size:11.2px;line-height:20px;color:var(--muted);text-align:justify}
.testi .sep{position:absolute;left:20px;right:20px;top:133px;height:1px;background:#ddd}
.avatar{position:absolute;left:20px;top:157px;width:44px;height:44px;border-radius:50%;background:linear-gradient(135deg,#c9a88b,#7a5a44)}
.testi .name{position:absolute;left:82px;top:162px;font-size:13px;color:var(--ink)}
.testi .loc{position:absolute;left:82px;top:181px;font-size:10.5px;color:var(--muted)}
.field{position:absolute;background:var(--white);border:1px solid #e6c98a;font-size:11.5px;color:#444;padding:0 14px;display:flex;align-items:center}
.arrow-circle{position:absolute;width:28px;height:28px;border-radius:50%;display:flex;align-items:center;justify-content:center}
</style>
</head>
<body>

<section class="panel" style="top:103px;height:913px;">
  <div class="photo" role="img" aria-label="Bright residence living room with sofa, shelves and wooden coffee table" style="left:0;top:0;width:507px;height:542px;background:linear-gradient(160deg,#d8d2c8 0%,#bdb3a3 45%,#8e8170 100%);"></div>
  <div class="photo" role="img" aria-label="Agent showing a couple an empty modern office space" style="left:507px;top:0;width:507px;height:542px;background:linear-gradient(160deg,#c7ccd2 0%,#9aa3ad 50%,#5c6672 100%);"></div>
  <div class="abs" style="left:0;top:0;width:1014px;height:542px;background:rgba(0,0,0,.28)"></div>

  <svg class="abs" style="left:393px;top:0" width="226" height="142" viewBox="0 0 226 142"><polygon points="0,0 226,0 226,96 113,142 0,96" fill="#fff"/></svg>
  <div class="c logo-name" style="left:506px;top:76px;font-size:19px;">Velmor Spire Nine</div>

  <div class="c split-title" style="left:253px;top:236px;">Velmor Spire Residence</div>
  <div class="c split-text" style="left:253px;top:284px;">Lorem ipsum dolor sit amet, consectetur adipiscing elit<br>sed do eiusmod tempor incidea.</div>
  <a class="btn btn-outline-light" style="left:196px;top:351px;width:116px;height:39px;">Learn More</a>

  <div class="c split-title" style="left:760px;top:236px;">Velmor Spire Office</div>
  <div class="c split-text" style="left:760px;top:284px;">Lorem ipsum dolor sit amet, consectetur adipiscing elit<br>sed do eiusmod tempor incidea.</div>
  <a class="btn btn-gold" style="left:703px;top:351px;width:116px;height:39px;">Learn More</a>

  <footer class="footer" style="top:542px;background:var(--ink)">
    <nav class="nav">
      <a style="left:93px">HOME</a><a style="left:156px">ABOUT US</a><a style="left:244px">OUR SERVICES</a>
      <a style="left:742px">RESOURCES</a><a style="left:841px">CONTACT US</a>
    </nav>
    <div class="rule" style="top:97px"></div>
    <div class="c logo-name" style="left:506px;top:132px;">Velmor Spire Nine</div>
    <div class="vdiv" style="left:369px"></div><div class="vdiv" style="left:645px"></div>

    <svg class="abs" style="left:220px;top:150px" width="20" height="24" viewBox="0 0 20 24"><path d="M10 1a8 8 0 0 0-8 8c0 6 8 14 8 14s8-8 8-14a8 8 0 0 0-8-8z" fill="#d19a26"/><circle cx="10" cy="9" r="3" fill="#1a1a1a"/></svg>
    <div class="c label" style="left:230px;top:192px;">LOCATION:</div>
    <div class="c info" style="left:230px;top:226px;">465, Lorum Ipsum Dolore Sed Amet,<br>United States</div>

    <svg class="abs" style="left:496px;top:191px" width="20" height="20" viewBox="0 0 24 24"><path d="M6.6 10.8a15 15 0 0 0 6.6 6.6l2.2-2.2a1 1 0 0 1 1-.25 11.4 11.4 0 0 0 3.6.6 1 1 0 0 1 1 1V20a1 1 0 0 1-1 1A17 17 0 0 1 3 4a1 1 0 0 1 1-1h3.5a1 1 0 0 1 1 1c0 1.25.2 2.45.6 3.6a1 1 0 0 1-.25 1z" fill="#d19a26"/></svg>
    <div class="c label" style="left:506px;top:234px;">PHONE:</div>
    <div class="c info" style="left:506px;top:268px;">+1 (555) 014 2276</div>

    <svg class="abs" style="left:771px;top:153px" width="24" height="18" viewBox="0 0 24 18"><rect width="24" height="18" rx="2" fill="#d19a26"/><path d="M1 2l11 8 11-8" stroke="#1a1a1a" stroke-width="2" fill="none"/></svg>
    <div class="c label" style="left:783px;top:192px;">EMAIL:</div>
    <div class="c info" style="left:783px;top:226px;">info@velmorspirenine.com</div>

    <div class="rule" style="top:305px"></div>
    <div class="c copy" style="left:506px;">© 2024 Velmor Spire Nine &nbsp;/&nbsp; All Rights Reserved &nbsp;/&nbsp; Privacy policy</div>
    <span class="social on" style="left:820px;top:318px"></span><span class="social" style="left:855px;top:318px"></span><span class="social" style="left:890px;top:318px"></span>
  </footer>
</section>

<section class="panel" style="top:1102px;height:3059px;">
  <div class="topbar">
    <svg class="abs" style="left:93px;top:14px" width="11" height="11" viewBox="0 0 24 24"><path d="M6.6 10.8a15 15 0 0 0 6.6 6.6l2.2-2.2a1 1 0 0 1 1-.25 11.4 11.4 0 0 0 3.6.6 1 1 0 0 1 1 1V20a1 1 0 0 1-1 1A17 17 0 0 1 3 4a1 1 0 0 1 1-1h3.5a1 1 0 0 1 1 1c0 1.25.2 2.45.6 3.6a1 1 0 0 1-.25 1z" fill="#d19a26"/></svg>
    <span class="abs" style="left:111px;top:13px">+1 (555) 014 2276</span>
    <svg class="abs" style="left:223px;top:15px" width="13" height="10" viewBox="0 0 24 18"><rect width="24" height="18" rx="2" fill="#d19a26"/></svg>
    <span class="abs" style="left:243px;top:13px">info@velmorspirenine.com</span>
    <span class="social" style="left:825px;top:7px;width:26px;height:26px;border-color:#d19a26"></span>
    <span class="social" style="left:858px;top:7px;width:26px;height:26px;border-color:#d19a26"></span>
    <span class="social" style="left:891px;top:7px;width:26px;height:26px;border-color:#d19a26"></span>
  </div>
  <nav class="mainnav">
    <a style="left:93px;color:var(--gold)">HOME</a>
    <span class="abs" style="left:145px;top:0;width:1px;height:66px;background:#eee"></span>
    <a style="left:163px">ABOUT US</a>
    <span class="abs" style="left:240px;top:0;width:1px;height:66px;background:#eee"></span>
    <a style="left:257px">OUR SERVICES</a>
    <a style="left:686px">RESOURCES</a>
    <a style="left:782px;width:135px;justify-content:center;background:var(--gold);color:var(--white)">CONTACT US</a>
  </nav>

  <div class="photo" role="img" aria-label="Agent showing a couple an empty modern office with tall windows" style="left:0;top:106px;width:1014px;height:545px;clip-path:polygon(0 0,100% 0,100% 73%,50% 100%,0 73%);background:linear-gradient(90deg,#d9d9d9 0%,#c9ccd0 35%,#9aa2ab 65%,#6a737d 100%);"></div>
  <svg class="abs" style="left:0;top:495px" width="1014" height="182" viewBox="0 0 1014 182"><polygon points="0,8 507,150 1014,8 1014,28 507,182 0,28" fill="#d19a26"/></svg>
  <svg class="abs" style="left:0;top:296px" width="14" height="24" viewBox="0 0 14 24"><polygon points="0,0 14,12 0,24" fill="#fff"/></svg>
  <svg class="abs" style="left:1000px;top:296px" width="14" height="24" viewBox="0 0 14 24"><polygon points="14,0 0,12 14,24" fill="#fff"/></svg>
  <h1 class="abs serif" style="left:93px;top:212px;font-size:40px;line-height:46px;font-weight:400;color:var(--ink)">Velmor Spire<br>Office</h1>
  <span class="underline" style="left:93px;top:308px;width:38px;"></span>
  <p class="abs" style="left:93px;top:328px;font-size:15.5px;line-height:26px;color:#333">Lorem ipsum dolor sit amet, consectetur adipis<br>sed do eiusmod tempor incididuntut.</p>
  <a class="btn btn-gold" style="left:93px;top:401px;width:124px;height:37px;">Get Started</a>

  <svg class="abs" style="left:427px;top:0" width="160" height="169" viewBox="0 0 160 169"><polygon points="0,0 160,0 160,130 80,169 0,130" fill="#fff"/></svg>
  <div class="c logo-name" style="left:507px;top:82px;font-size:16px;">Velmor Spire Nine</div>

  <div class="abs" style="left:93px;top:749px;width:393px;height:325px;border:1.5px solid #e0c48a"></div>
  <div class="photo" role="img" aria-label="Smiling consultant in an orange blazer meeting a client at a desk" style="left:116px;top:772px;width:391px;height:325px;background:linear-gradient(120deg,#e8e6e3 0%,#d7d2cc 45%,#c46a3a 70%,#a9502a 100%);"></div>
  <h2 class="abs h-section" style="left:541px;top:760px;">About Us</h2>
  <span class="underline" style="left:753px;top:781px;width:40px;height:2px"></span>
  <p class="abs body-p" style="left:541px;top:819px;width:380px">Lorem ipsum dolor sit amet, consectetur adipiscing elit, sed do eiusmod tempor incididunt ut labore et dolore magna aliqua. Ut enim ad minim veniam, quis nostrud exercitation ullamco laboris nisi ut aliquidiunt ut laboripea.</p>
  <p class="abs body-p" style="left:541px;top:919px;width:380px">Sed um dolor sit amet, consectetur adipiscing elit, sed do eiusmod tempor incididunt ut labore et dolore magna aliqua. Ut enim ad minim veniam, quis nostrud exercitation ullamco laboris nisi ut aliquiis nostrud exercdolore magna aliquaitpea.</p>
  <a class="btn btn-outline-gold" style="left:541px;top:1033px;width:114px;height:43px;">Learn More</a>

  <div class="abs" style="left:0;top:1202px;width:1014px;height:520px;background:var(--soft)"></div>
  <h2 class="c h-section" style="left:507px;top:1259px;">Our Solutions</h2>
  <span class="underline" style="left:487px;top:1310px;width:40px;height:2px"></span>
  <div class="arrow-circle" style="left:29px;top:1469px;background:#e4e4e4"><svg width="8" height="10" viewBox="0 0 8 10"><path d="M6 1L2 5l4 4" stroke="#333" stroke-width="1.6" fill="none"/></svg></div>
  <div class="arrow-circle" style="left:955px;top:1469px;background:var(--gold)"><svg width="8" height="10" viewBox="0 0 8 10"><path d="M2 1l4 4-4 4" stroke="#fff" stroke-width="1.6" fill="none"/></svg></div>
  <article class="card solution" style="left:93px"><div class="tag">LOREM IPSUM DOLOR</div><p>Lorem ipsum dolor sit amet, consectetur adipiscing elit, sed do eiusmod tempor incididunt ut laborea.</p><div class="photo" role="img" aria-label="Office floor with dark blue wall and workstations" style="background:linear-gradient(135deg,#2e4658 0%,#c9cdd0 55%,#e5e6e6 100%)"></div></article>
  <article class="card solution" style="left:377px"><div class="tag">LOREM IPSUM DOLOR</div><p>Lorem ipsum dolor sit amet, consectetur adipiscing elit, sed do eiusmod tempor incididunt ut laborea.</p><div class="photo" role="img" aria-label="Bright open-plan office with white desks" style="background:linear-gradient(135deg,#e4e4e4 0%,#bfbfbf 55%,#6f6f6f 100%)"></div></article>
  <article class="card solution" style="left:661px"><div class="tag">LOREM IPSUM DOLOR</div><p>Lorem ipsum dolor sit amet, consectetur adipiscing elit, sed do eiusmod tempor incididunt ut laborea.</p><div class="photo" role="img" aria-label="Modern office with glass windows and black chairs" style="background:linear-gradient(135deg,#3a3f45 0%,#d8dde2 50%,#9fb4c4 100%)"></div></article>

  <h2 class="c h-section" style="left:507px;top:1803px;">Testimonials</h2>
  <span class="underline" style="left:487px;top:1847px;width:40px;height:2px"></span>
  <article class="card testi" style="left:93px"><div class="stars">★★★★★</div><p>Lorem ipsum dolor sit amet, consectetur adipiscing elit, sed do eiusmod tempor incididunt ut labore et dolore magna aliqu ad minim veniam, quisea.</p><div class="sep"></div><div class="avatar" role="img" aria-label="Client portrait"></div><div class="name">OWEN HARLOW,</div><div class="loc">United States</div></article>
  <article class="card testi" style="left:377px"><div class="stars">★★★★★</div><p>Lorem ipsum dolor sit amet, consectetur adipiscing elit, sed do eiusmod tempor incididunt ut labore et dolore magna aliqu ad minim veniam, quisea.</p><div class="sep"></div><div class="avatar" role="img" aria-label="Client portrait"></div><div class="name">MIRA DALTON,</div><div class="loc">United States</div></article>
  <article class="card testi" style="left:661px"><div class="stars">★★★★★</div><p>Lorem ipsum dolor sit amet, consectetur adipiscing elit, sed do eiusmod tempor incididunt ut labore et dolore magna aliqu ad minim veniam, quisea.</p><div class="sep"></div><div class="avatar" role="img" aria-label="Client portrait"></div><div class="name">OWEN HARLOW,</div><div class="loc">United States</div></article>
  <div class="abs" style="left:475px;top:2139px;display:flex;gap:10px">
    <span style="width:8px;height:8px;border-radius:50%;background:#ddd"></span><span style="width:8px;height:8px;border-radius:50%;background:var(--gold)"></span><span style="width:8px;height:8px;border-radius:50%;background:#ddd"></span><span style="width:8px;height:8px;border-radius:50%;background:#ddd"></span>
  </div>

  <div class="photo" role="img" aria-label="Business handshake over a desk, tinted gold" style="left:0;top:2221px;width:1014px;height:560px;background:linear-gradient(135deg,#c98f1e 0%,#d9a33a 40%,#c28a20 70%,#b8801a 100%)"></div>
  <h2 class="c serif" style="left:507px;top:2275px;font-size:32px;font-weight:400;color:var(--white)">INQUIRY</h2>
  <span class="underline" style="left:487px;top:2320px;width:40px;height:2px;background:var(--white)"></span>
  <div class="field" style="left:139px;top:2354px;width:239px;height:42px">Full Name</div>
  <div class="field" style="left:388px;top:2354px;width:239px;height:42px">Phone</div>
  <div class="field" style="left:637px;top:2354px;width:240px;height:42px">Email Address</div>
  <div class="field" style="left:139px;top:2406px;width:738px;height:78px;align-items:flex-start;padding-top:12px">Message</div>
  <a class="btn btn-dark" style="left:432px;top:2500px;width:150px;height:41px;">Send Message</a>

  <svg class="abs" style="left:0;top:2573px" width="1014" height="200" viewBox="0 0 1014 200"><polygon points="0,186 507,0 1014,186 1014,200 0,200" fill="#fff"/><polygon points="0,200 507,12 1014,200" fill="#1a1a1a"/></svg>

  <footer class="footer" style="top:2695px;">
    <div class="abs" style="left:0;top:70px;width:1014px;height:301px;background:var(--ink)"></div>
    <nav class="nav">
      <a style="left:93px">HOME</a><a style="left:156px">ABOUT US</a><a style="left:244px">OUR SERVICES</a>
      <a style="left:742px">RESOURCES</a><a style="left:841px">CONTACT US</a>
    </nav>
    <div class="rule" style="top:97px"></div>
    <div class="c logo-name" style="left:506px;top:132px;">Velmor Spire Nine</div>
    <div class="vdiv" style="left:369px"></div><div class="vdiv" style="left:645px"></div>

    <svg class="abs" style="left:220px;top:150px" width="20" height="24" viewBox="0 0 20 24"><path d="M10 1a8 8 0 0 0-8 8c0 6 8 14 8 14s8-8 8-14a8 8 0 0 0-8-8z" fill="#d19a26"/><circle cx="10" cy="9" r="3" fill="#1a1a1a"/></svg>
    <div class="c label" style="left:230px;top:192px;">LOCATION:</div>
    <div class="c info" style="left:230px;top:226px;">465, Lorum Ipsum Dolore Sed Amet,<br>United States</div>

    <svg class="abs" style="left:496px;top:191px" width="20" height="20" viewBox="0 0 24 24"><path d="M6.6 10.8a15 15 0 0 0 6.6 6.6l2.2-2.2a1 1 0 0 1 1-.25 11.4 11.4 0 0 0 3.6.6 1 1 0 0 1 1 1V20a1 1 0 0 1-1 1A17 17 0 0 1 3 4a1 1 0 0 1 1-1h3.5a1 1 0 0 1 1 1c0 1.25.2 2.45.6 3.6a1 1 0 0 1-.25 1z" fill="#d19a26"/></svg>
    <div class="c label" style="left:506px;top:234px;">PHONE:</div>
    <div class="c info" style="left:506px;top:268px;">+1 (555) 014 2276</div>

    <svg class="abs" style="left:771px;top:153px" width="24" height="18" viewBox="0 0 24 18"><rect width="24" height="18" rx="2" fill="#d19a26"/><path d="M1 2l11 8 11-8" stroke="#1a1a1a" stroke-width="2" fill="none"/></svg>
    <div class="c label" style="left:783px;top:192px;">EMAIL:</div>
    <div class="c info" style="left:783px;top:226px;">info@velmorspirenine.com</div>

    <div class="rule" style="top:305px"></div>
    <div class="c copy" style="left:506px;">© 2024 Velmor Spire Nine &nbsp;/&nbsp; All Rights Reserved &nbsp;/&nbsp; Privacy policy</div>
    <span class="social on" style="left:820px;top:318px"></span><span class="social" style="left:855px;top:318px"></span><span class="social" style="left:890px;top:318px"></span>
  </footer>
</section>

</body>
</html>
```